Create a captivating door hanger for a holiday lighting company!

We need a beautiful 4.25x11 standard die cut door hanger that makes people want to call us or visit our website! It needs to be two-sided, in full color, with our logo, website, phone number, and a QR code (that goes to our website). We will provide the logo and one photo that must be used, but the rest is up to you. Our brand is sleek and sophisticated, but still warm and inviting.

Company Name: Fernwick Yuletide Glow
Website: www.fernwickglow.example
Phone: 612.394.7180

Verbiage to incorporate

Tag line: "Shine Brightly this Season with Fernwick Yuletide Glow"

Why they should choose us:

Customized Designs: Our talented designers craft light displays that complement your style and architecture.

Professional Installation: Stay cozy indoors while we handle the heights and heavy lifting. Our experienced team will create a magical transformation!

Hassle-Free Storage: No more boxes taking up space... We carefully maintain and store our commercial-grade lights and make them ready to dazzle you again next year!

Call to Action: "Limited spots available. Reserve your light installation today!"

```html
<!DOCTYPE html>
<html lang="en">
<head>
<meta charset="utf-8">
<title>Fernwick Yuletide Glow – Door Hanger</title>
<link rel="stylesheet" href="https://fonts.googleapis.com/css2?family=Nunito+Sans:wght@300;400;800&family=Arimo:wght@700&display=swap">
<style>
  :root{
    --page:#ffffff;
    --navy:#10151f;
    --gold:#f1d98c;
    --gold-line:#c8ad63;
    --white:#ffffff;
  }
  *{box-sizing:border-box;margin:0;padding:0}
  html,body{width:1200px;height:1200px;overflow:hidden;background:var(--page)}
  body{position:relative;font-family:"Nunito Sans",sans-serif;color:var(--white)}
  .hanger{position:absolute;top:65px;width:405px;height:1049px;background:var(--navy);overflow:hidden;box-shadow:0 2px 6px rgba(0,0,0,.15)}
  .hanger--front{left:144px}
  .hanger--back{left:660px}
  .hanger__hole{position:absolute;left:138px;top:66px;width:130px;height:130px;border-radius:50%;background:var(--page);z-index:3}
  .abs{position:absolute}

  /* front */
  .house-photo{left:0;top:0;width:405px;height:590px;
    background:linear-gradient(180deg,#2b4680 0%,#43577f 22%,#8a8570 42%,#d9cf9c 58%,#b7a77a 75%,#6f8a45 88%,#4f7a32 100%)}
  .gold-rule{left:0;top:589px;width:405px;height:3px;background:var(--gold-line)}
  .lights-band{left:0;top:592px;width:405px;height:120px;
    background:radial-gradient(ellipse at 15% 40%,rgba(255,190,70,.35),transparent 45%),
               radial-gradient(ellipse at 85% 40%,rgba(255,190,70,.35),transparent 45%)}
  .brand{left:0;width:405px;top:668px;display:flex;align-items:center;justify-content:center;gap:12px;
    font-weight:300;font-size:25px;letter-spacing:1.5px;text-transform:uppercase;color:var(--white)}
  .brand__mark{width:14px;height:14px;border:2px solid var(--gold-line)}
  .tagline{left:0;width:405px;top:773px;text-align:center;font-weight:300;font-size:23px;line-height:29px;color:var(--gold)}
  .cta-title{font-weight:800;font-size:29px;letter-spacing:.2px;color:var(--white)}
  .cta-sub{font-weight:400;font-size:20px;color:var(--white)}
  .front .cta-title{left:0;width:405px;text-align:center;top:856px}
  .front .cta-sub{left:0;width:405px;text-align:center;top:898px}
  .phone-box{border:2px solid var(--gold-line);display:flex;align-items:center;justify-content:center;
    font-family:"Arimo",sans-serif;font-weight:700;color:var(--gold);letter-spacing:1px}
  .front .phone-box{left:28px;top:935px;width:350px;height:76px;font-size:47px}

  /* back */
  .string-lights{left:0;top:0;width:405px;height:290px;
    background:radial-gradient(circle at 85% 30%,rgba(255,190,70,.45),transparent 35%),
               radial-gradient(circle at 40% 75%,rgba(255,190,70,.4),transparent 40%),
               radial-gradient(circle at 10% 20%,rgba(255,190,70,.2),transparent 30%),var(--navy)}
  .feature{left:40px;width:350px;display:flex;gap:15px}
  .feature__icon{flex:none;width:60px;height:60px}
  .feature__text{font-weight:400;font-size:19.5px;line-height:24px;color:var(--white)}
  .feature__title{display:block;font-weight:800;font-size:19.5px;color:var(--gold)}
  .back .cta-title{left:29px;top:821px;font-size:30px}
  .back .cta-sub{left:29px;top:859px}
  .back .phone-box{left:28px;top:906px;width:350px;height:67px;font-size:44px}
  .website{left:0;width:405px;top:988px;text-align:center;font-size:20px;letter-spacing:1.2px;color:var(--white)}
</style>
</head>
<body>

<section class="hanger hanger--front front">
  <div class="hanger__hole"></div>
  <div class="abs house-photo" role="img" aria-label="Photo of a white two-storey house outlined in warm white holiday lights at dusk"></div>
  <div class="abs gold-rule"></div>
  <div class="abs lights-band" role="img" aria-label="Glowing strings of warm lights"></div>
  <div class="abs brand"><span class="brand__mark"></span>Fernwick Yuletide Glow</div>
  <p class="abs tagline">Shine brightly this season with<br>Fernwick Yuletide Glow</p>
  <h2 class="abs cta-title">Limited spots available.</h2>
  <p class="abs cta-sub">Reserve your light installation today!</p>
  <div class="abs phone-box">612.394.7180</div>
</section>

<section class="hanger hanger--back back">
  <div class="hanger__hole"></div>
  <div class="abs string-lights" role="img" aria-label="Strings of glowing golden bulbs against a dark sky"></div>

  <div class="abs feature" style="top:285px">
    <svg class="feature__icon" viewBox="0 0 60 60" aria-hidden="true">
      <circle cx="30" cy="30" r="28" fill="none" stroke="var(--gold)" stroke-width="2"/>
      <path d="M30 17a9 9 0 0 0-5 16.5V37h10v-3.5A9 9 0 0 0 30 17z" fill="var(--gold)"/>
      <rect x="25.5" y="39" width="9" height="3" fill="var(--gold)"/>
      <rect x="27" y="43.5" width="6" height="2.5" fill="var(--gold)"/>
      <path d="M17 20l3 2M43 20l-3 2M15 29h4M45 29h-4" stroke="var(--gold)" stroke-width="2"/>
    </svg>
    <p class="feature__text"><span class="feature__title">Customized Designs:</span>Our talented designers craft light displays that complement your style and architecture.</p>
  </div>

  <div class="abs feature" style="top:428px">
    <svg class="feature__icon" viewBox="0 0 60 60" aria-hidden="true">
      <circle cx="30" cy="30" r="28" fill="none" stroke="var(--gold)" stroke-width="2"/>
      <path d="M19 41l18-18" stroke="var(--white)" stroke-width="4" stroke-linecap="round"/>
      <circle cx="39" cy="21" r="5" fill="none" stroke="var(--white)" stroke-width="3"/>
      <path d="M20 19l21 22" stroke="var(--white)" stroke-width="4" stroke-linecap="round"/>
    </svg>
    <p class="feature__text"><span class="feature__title">Professional Installation:</span>Stay cozy indoors while we handle the heights and heavy lifting. Our experi-enced team will create a magical transformation!</p>
  </div>

  <div class="abs feature" style="top:595px">
    <svg class="feature__icon" viewBox="0 0 60 60" aria-hidden="true">
      <circle cx="30" cy="30" r="28" fill="none" stroke="var(--gold)" stroke-width="2"/>
      <path d="M30 16l12 6v14l-12 6-12-6V22z" fill="var(--gold)"/>
      <path d="M18 22l12 6 12-6M30 28v14" stroke="var(--navy)" stroke-width="2" fill="none"/>
      <path d="M12 12l36 36" stroke="var(--white)" stroke-width="2.5"/>
    </svg>
    <p class="feature__text"><span class="feature__title">Hassle-Free Storage:</span>No more boxes taking up space... We carefully main-tain and store our commer-cial-grade lights and make them ready to dazzle you again next year!</p>
  </div>

  <h2 class="abs cta-title">Limited spots available.</h2>
  <p class="abs cta-sub">Reserve your light installation today!</p>
  <div class="abs phone-box">612.394.7180</div>
  <p class="abs website">www.fernwickglow.example</p>
</section>

</body>
</html>
```